Transform Your Giving

I need a tri-fold brochure that will fit in a standard number 10 business envelope. Meadowlark and Allied Services is a charitable nonprofit. The goal of this brochure is to stimulate people into thinking about other ways to make a donation. The design should communicate the essential information on donation options, create a sense of professional integrity, be graphically sharp, easy to read and laid out in a way that doesn't make the material appear crowded.

```html
<!DOCTYPE html>
<html lang="en">
<head>
<meta charset="utf-8">
<title>Transform Your Giving – Meadowlark and Allied Services</title>
<link rel="stylesheet" href="https://fonts.googleapis.com/css2?family=Fira+Sans:ital,wght@0,400;0,500;0,600;0,700;1,600;1,700&family=Source+Sans+3:ital,wght@0,400;0,600;1,400&display=swap">
<style>
:root{
  --navy:#29246f;
  --navy-panel:#2e2a78;
  --green:#4cb748;
  --ink:#2a2a35;
  --paper:#ffffff;
  --backdrop:#7b7b7b;
  --muted:#b5b5bb;
}
*{box-sizing:border-box;margin:0;padding:0}
html,body{width:1096px;height:1200px;overflow:hidden;background:var(--backdrop)}
body{position:relative;font-family:"Source Sans 3",sans-serif;color:var(--ink)}
.sheet{position:absolute;left:205px;width:687px;height:516px;display:flex;background:var(--paper)}
.sheet--outside{top:63px}
.sheet--inside{top:621px}
.panel{position:relative;width:229px;height:516px;overflow:hidden}
.panel--navy{background:var(--navy-panel);color:#fff}
.photo{position:absolute;left:0;width:229px}
.curve{position:absolute;left:0;width:229px;height:34px;display:block}
.h-sans{font-family:"Fira Sans",sans-serif}

/* outside left */
.impact{position:absolute;left:18px;top:275px;width:200px}
.impact__title{font-family:"Fira Sans",sans-serif;font-weight:700;color:var(--navy);font-size:11.5px;letter-spacing:.1px}
.impact__text{font-family:"Fira Sans",sans-serif;font-size:9.7px;line-height:1.35;color:#222;margin-top:2px}
.checks{position:absolute;left:18px;top:407px;display:grid;grid-template-columns:58px 120px;row-gap:6px;font-family:"Fira Sans",sans-serif;font-weight:500;font-size:10px;color:#222}
.checks li{list-style:none;display:flex;align-items:center;gap:5px}
.tick{width:8px;height:8px;flex:none}
.wordmark{font-family:"Fira Sans",sans-serif;font-weight:700;text-align:center}
.wordmark--faint{position:absolute;left:80px;top:473px;width:135px;font-size:10px;line-height:1.15;color:var(--muted)}

/* outside middle */
.lead{position:absolute;left:14px;top:17px;width:201px;text-align:center;font-family:"Fira Sans",sans-serif;font-weight:600;font-size:8.6px;line-height:1.36}
.quote{position:absolute;left:14px;top:92px;width:201px;text-align:center;font-style:italic;font-size:9px;line-height:1.3;font-weight:400}
.will{position:absolute;left:10px;top:224px;width:209px;text-align:center;font-size:8.8px;line-height:1.3}
.will a{color:var(--green);text-decoration:underline}
.wordmark--panel{position:absolute;left:20px;top:276px;width:189px;font-size:14px;line-height:1.15;color:#fff}
.contact{position:absolute;left:10px;top:338px;width:209px;text-align:center}
.contact__title{font-family:"Fira Sans",sans-serif;font-weight:700;font-size:10.5px;text-decoration:underline}
.contact__sub{font-family:"Fira Sans",sans-serif;font-weight:600;font-size:8.6px;color:var(--green);line-height:1.3;margin-top:5px}
.contact__item{font-size:8.3px;line-height:1.3;margin-top:3px}
.dot{display:block;margin:4px auto 1px;width:7px;height:7px}
.follow{margin-top:6px;display:flex;justify-content:center;align-items:center;gap:3px;font-family:"Fira Sans",sans-serif;font-weight:700;font-size:8.6px}
.follow span{text-decoration:underline;margin-right:2px}
.follow i{display:block;width:9px;height:9px;border-radius:50%;background:var(--green)}

/* outside right */
.cover__title{position:absolute;top:13px;left:0;width:229px;text-align:center;font-family:"Fira Sans",sans-serif;font-weight:600;font-size:17px;line-height:1.15;color:var(--navy)}
.cover__title em{font-style:normal;color:var(--green);display:block}
.cover__sub{position:absolute;top:57px;left:10px;width:209px;text-align:center;font-family:"Fira Sans",sans-serif;font-weight:600;font-size:8.5px;line-height:1.35;color:var(--navy)}
.options{position:absolute;left:0;top:0;width:229px;height:516px}
.opt-label{position:absolute;font-family:"Fira Sans",sans-serif;font-weight:600;font-size:10px;line-height:1.3;color:#222;text-align:center;width:80px}
.wordmark--cover{position:absolute;left:20px;top:448px;width:189px;font-size:15px;line-height:1.15;color:var(--navy)}

/* inside */
.col{padding:20px 16px 0 18px}
.intro{font-family:"Fira Sans",sans-serif;font-weight:500;font-size:8.8px;line-height:1.32;color:#222}
.feature{display:grid;grid-template-columns:52px 1fr;column-gap:5px;margin-top:9px;align-items:start}
.badge{width:52px;height:52px}
.feature__title{font-family:"Fira Sans",sans-serif;font-weight:600;font-size:9.2px;line-height:1.25;color:var(--navy)}
.feature__pitch{font-family:"Fira Sans",sans-serif;font-weight:600;font-style:italic;font-size:8.7px;line-height:1.28;color:var(--green);margin-top:2px}
.body{font-size:8.6px;line-height:1.28;color:#2c2c2c;margin-top:3px}
.body--lg{font-size:9.4px;line-height:1.27}
.how{font-family:"Fira Sans",sans-serif;font-weight:600;font-size:10.5px;color:var(--navy);margin-top:7px}
.bullets{margin-top:7px}
.bullets li{list-style:none;position:relative;padding-left:10px;font-size:8.4px;line-height:1.27;margin-bottom:5px}
.bullets svg{position:absolute;left:0;top:2px;width:7px;height:7px}
</style>
</head>
<body>
<svg width="0" height="0" style="position:absolute" aria-hidden="true">
  <defs>
    <symbol id="ic-coin" viewBox="0 0 40 40"><g fill="none" stroke="#fff" stroke-width="1.8"><circle cx="20" cy="20" r="11"/><circle cx="20" cy="20" r="7"/><path d="M20 9v4M20 27v4M9 20h4M27 20h4"/></g></symbol>
    <symbol id="ic-bank" viewBox="0 0 40 40"><g fill="none" stroke="#fff" stroke-width="1.8" stroke-linejoin="round"><path d="M9 15 20 9l11 6z"/><path d="M10 17h20M10 29h20M8 31h24"/><path d="M13 18v10M18 18v10M22 18v10M27 18v10"/></g></symbol>
    <symbol id="ic-gift" viewBox="0 0 40 40"><g fill="none" stroke="#fff" stroke-width="1.8" stroke-linejoin="round"><rect x="10" y="18" width="20" height="13"/><rect x="9" y="14" width="22" height="4"/><path d="M20 14v17M20 14c-3-5-8-4-6-1 1 1 6 1 6 1zM20 14c3-5 8-4 6-1-1 1-6 1-6 1z"/></g></symbol>
    <symbol id="ic-chart" viewBox="0 0 40 40"><g fill="none" stroke="#fff" stroke-width="1.8" stroke-linejoin="round"><rect x="10" y="23" width="4" height="7"/><rect x="17" y="19" width="4" height="11"/><rect x="24" y="15" width="4" height="15"/><path d="M8 31h24M9 20 25 10M21 10h4v4"/></g></symbol>
    <symbol id="ic-annuity" viewBox="0 0 40 40"><g fill="none" stroke="#fff" stroke-width="1.6"><rect x="9" y="11" width="22" height="19" rx="1.5"/><path d="M9 16h22M13 9v4M27 9v4"/><circle cx="20" cy="17" r="4" fill="#29246f"/><path d="M20 15v4"/><path d="M12 22h2M17 22h2M22 22h2M27 22h1M12 26h2M17 26h2M22 26h2M27 26h1"/></g></symbol>
    <symbol id="ic-tick" viewBox="0 0 10 10"><circle cx="5" cy="5" r="5" fill="#29246f"/><path d="M2.8 5.2 4.4 6.7 7.3 3.6" fill="none" stroke="#fff" stroke-width="1.3"/></symbol>
    <symbol id="ic-dot" viewBox="0 0 10 10"><circle cx="5" cy="5" r="5" fill="#4cb748"/><circle cx="5" cy="5" r="1.8" fill="#2e2a78"/></symbol>
    <symbol id="badge-ring" viewBox="0 0 52 52"><circle cx="26" cy="26" r="25" fill="#fff" stroke="#4cb748" stroke-width="2.4"/><circle cx="26" cy="26" r="21" fill="#29246f"/></symbol>
    <symbol id="cover-ring" viewBox="0 0 44 44"><circle cx="22" cy="22" r="21" fill="#29246f"/><circle cx="22" cy="22" r="18.5" fill="none" stroke="#fff" stroke-width="1"/></symbol>
  </defs>
</svg>

<!-- Outside of the brochure -->
<section class="sheet sheet--outside">
  <article class="panel panel--impact">
    <div class="photo" style="top:0;height:280px;background:linear-gradient(135deg,#8e8d88 0%,#d9c2a8 45%,#b9b0a6 75%,#6d6b66 100%)" role="img" aria-label="Photo of a caregiver holding hands with a smiling elderly woman in a wheelchair"></div>
    <svg class="curve" style="top:250px" viewBox="0 0 229 34" preserveAspectRatio="none" aria-hidden="true">
      <path d="M0 30Q110 -4 229 30V34H0Z" fill="#fff"/>
      <path d="M0 30Q110 -4 229 30Q110 4 0 30Z" fill="#4cb748"/>
    </svg>
    <div class="impact">
      <h2 class="impact__title">THE IMPACT OF YOUR GIFT</h2>
      <p class="impact__text">Your generosity drives our mission. With every Smart gift you’re supporting Meadowlark and Allied Services. Join our community of Smart Givers today and make an enduring impact. With Smart Giving your generosity reaches further.&nbsp; Begin your Smart Giving journey with us today.</p>
    </div>
    <ul class="checks">
      <li><svg class="tick"><use href="#ic-tick"/></svg>DAFs</li>
      <li><svg class="tick"><use href="#ic-tick"/></svg>Stocks and Securities</li>
      <li><svg class="tick"><use href="#ic-tick"/></svg>QCDs</li>
      <li><svg class="tick"><use href="#ic-tick"/></svg>Charitable Annuity</li>
      <li><svg class="tick"><use href="#ic-tick"/></svg>Crypto</li>
    </ul>
    <p class="wordmark wordmark--faint">Meadowlark and Allied Services</p>
  </article>

  <article class="panel panel--navy">
    <p class="lead">To learn more about Smart Giving Options and how they can benefit you and Meadowlark and Allied Services, please reach out to our team.&nbsp; We’re here to help you navigate these giving methods and answer any question you may have.</p>
    <p class="quote">Being kind to others is a way of<br>being good to yourself.<br>Ruth Ellington</p>
    <div class="photo" style="top:122px;height:98px;background:linear-gradient(160deg,rgba(46,42,120,0) 30%,#e8a27c 55%,#f3c2a0 75%,#e59b72 100%)" role="img" aria-label="Close-up photo of a younger hand holding an elderly hand"></div>
    <p class="will">If you do not have a will, go to<br><a>www.EasyWillNow.com.</a><br>In 20 minutes you can have a legal will – for free.</p>
    <p class="wordmark wordmark--panel">Meadowlark and Allied Services</p>
    <div class="contact">
      <h3 class="contact__title">CONTACT US</h3>
      <p class="contact__sub">Have more question? Please contact us at<br>Meadowlark and Allied Services</p>
      <svg class="dot"><use href="#ic-dot"/></svg>
      <p class="contact__item">2150 Prairie View Ave.<br>Suite 4 Fargo, ND&nbsp; 58102</p>
      <svg class="dot"><use href="#ic-dot"/></svg>
      <p class="contact__item">701-555-0148 (ext. 100)</p>
      <svg class="dot"><use href="#ic-dot"/></svg>
      <p class="contact__item">jmarlow@meadowlarkas.org</p>
      <svg class="dot"><use href="#ic-dot"/></svg>
      <p class="contact__item">www.meadowlarkas.org</p>
      <p class="follow"><span>FOLLOW US:</span><i></i><i></i></p>
    </div>
  </article>

  <article class="panel panel--cover">
    <h1 class="cover__title">Transform Your Giving<em>Be Strategic, Be Smart</em></h1>
    <p class="cover__sub">Discover the impact of Smart Giving with<br>Meadowlark and Allied Services</p>
    <div class="photo" style="top:88px;height:210px;background:linear-gradient(120deg,#5f8a3c 0%,#9db06b 35%,#c9c1b4 55%,#6b6f78 80%,#4d4a48 100%)" role="img" aria-label="Photo of a nurse holding the hand of a laughing elderly woman outdoors"></div>
    <svg class="curve" style="top:86px" viewBox="0 0 229 34" preserveAspectRatio="none" aria-hidden="true">
      <path d="M0 0H229V20Q114 -8 0 20Z" fill="#fff"/>
      <path d="M0 20Q114 -8 229 20Q114 -2 0 20Z" fill="#4cb748"/>
    </svg>
    <svg class="curve" style="top:268px" viewBox="0 0 229 34" preserveAspectRatio="none" aria-hidden="true">
      <path d="M0 28Q110 -6 229 28V34H0Z" fill="#fff"/>
      <path d="M0 28Q110 -6 229 28Q110 2 0 28Z" fill="#4cb748"/>
    </svg>
    <svg class="options" viewBox="0 0 229 516" aria-hidden="true">
      <g stroke="#29246f" stroke-width="1.2" stroke-dasharray="1.5 1.5">
        <line x1="66" y1="310" x2="95" y2="310"/><line x1="137" y1="310" x2="162" y2="310"/>
        <line x1="99" y1="370" x2="131" y2="370"/>
      </g>
      <use href="#cover-ring" x="24" y="289" width="42" height="42"/><use href="#ic-coin" x="27" y="292" width="36" height="36"/>
      <use href="#cover-ring" x="95" y="289" width="42" height="42"/><use href="#ic-bank" x="98" y="292" width="36" height="36"/>
      <use href="#cover-ring" x="162" y="289" width="42" height="42"/><use href="#ic-gift" x="165" y="292" width="36" height="36"/>
      <use href="#cover-ring" x="57" y="349" width="42" height="42"/><use href="#ic-chart" x="60" y="352" width="36" height="36"/>
      <use href="#cover-ring" x="131" y="349" width="42" height="42"/><use href="#ic-annuity" x="134" y="352" width="36" height="36"/>
    </svg>
    <p class="opt-label" style="left:5px;top:334px">CRYPTO</p>
    <p class="opt-label" style="left:76px;top:334px">DAF’S</p>
    <p class="opt-label" style="left:143px;top:334px">QCDS</p>
    <p class="opt-label" style="left:38px;top:394px">STOCKS &amp;<br>SECURITIES</p>
    <p class="opt-label" style="left:112px;top:394px">CHARITABLE<br>ANNUITY</p>
    <p class="wordmark wordmark--cover">Meadowlark and Allied Services</p>
  </article>
</section>

<!-- Inside of the brochure -->
<section class="sheet sheet--inside">
  <article class="panel col">
    <p class="intro">We would like to introduce you to five Strategic and Smart ways to give that could potentially be more beneficial to you compared to traditional cash donations. We encourage you to keep this information as a guide for your future contributions.</p>
    <div class="feature">
      <svg class="badge"><use href="#badge-ring"/><use href="#ic-chart" x="9" y="9" width="34" height="34"/></svg>
      <div>
        <h3 class="feature__title">Gifts of Stocks or Appreciated Assets Strategic &amp; Smart</h3>
        <p class="feature__pitch">Consider your long-term publicly traded stock as a way to give to your favorite charity.</p>
      </div>
    </div>
    <p class="body">You can make a significantly bigger impact when you donate long-term appreciated securities, including stock, mutual funds, &amp; bonds, directly to your favorite charity.</p>
    <h4 class="how">How Does It Work?</h4>
    <p class="body">When you donate stock to a charity, you will generally take a tax deduction for the full market value. Because you are donating stock, your contribution &amp; tax deduction may be significantly higher than contributing the after-tax proceeds. The same benefits apply when you donate mutual funds or bonds.</p>
    <div class="feature" style="margin-top:13px">
      <svg class="badge"><use href="#badge-ring"/><use href="#ic-bank" x="9" y="9" width="34" height="34"/></svg>
      <div>
        <h3 class="feature__title">Donor-Advised Fund (DAF)<br>Strategic &amp; Smart</h3>
        <p class="feature__pitch">Consider a DAF – a simple, flexible, and tax-advantageous way to give to your favorite charities.</p>
      </div>
    </div>
    <p class="body">A Donor-Advised Fund (DAF), is like a charitable investment account for the sole purpose of supporting your favorite charities.</p>
    <h4 class="how">How Does It Work?</h4>
    <p class="body">You establish a DAF &amp; contribute cash, stocks, or non-publicly traded assets, cryptocurrency, &amp; private company stock to be eligible for an immediate tax deduction. Those funds are contributed for tax-free growth. You can recommend grants be made from your DAF to any IRS qualified public charity.</p>
  </article>

  <article class="panel col">
    <div class="feature" style="margin-top:-3px">
      <svg class="badge"><use href="#badge-ring"/><use href="#ic-gift" x="9" y="9" width="34" height="34"/></svg>
      <div>
        <h3 class="feature__title">Qualified Charitable Distributions (QCDs) Strategic &amp; Smart</h3>
        <p class="feature__pitch">Consider a QCD – when planning your IRA withdrawal strategy… &amp; donate to your favorite charity.</p>
      </div>
    </div>
    <p class="body">IRA owners at age 70 ½ or over can transfer dollars from their IRA to charity tax-free each year. These transfers known as Qualified Charitable Distributions (QCDs) offer eligible older Americans a great way to easily give to charity.</p>
    <h4 class="how">How Does It Work?</h4>
    <p class="body">Are you 72 and required to take a minimum distribution (RMD) from your IRA but do not need the funds? Consider a Qualified Charitable Distribution. Normally, distributions from a traditional IRA are taxable when received. With a QCD, these distributions become tax-free when paid directly from the IRA to your favorite eligible charity. An IRA owner wishing to make a QCD should contact their IRA trustee, allowing time to complete the transaction before the end of the year to receive the tax benefit.</p>
    <div class="feature" style="margin-top:16px">
      <svg class="badge"><use href="#badge-ring"/><use href="#ic-annuity" x="9" y="9" width="34" height="34"/></svg>
      <div>
        <h3 class="feature__title">Charitable Gift Annuity<br>Strategic &amp; Smart</h3>
        <p class="feature__pitch">Consider establishing a<br>Charitable Gift Annuity</p>
      </div>
    </div>
    <p class="body">You make a donation to a single charity. The gift is set aside in a reserve account and invested.</p>
    <h4 class="how">How Does It Work?</h4>
    <p class="body">A charitable gift annuity is a contract between a donor &amp; a charity. As a donor, you make a sizable gift to charity using cash, securities, or possibly other assets. This money is then invested. In return, you become eligible to take a partial tax deduction for your donation, plus you receive a fixed stream of income from the charity for the rest of your life. At the end of your life (as well as your spouse’s, if you’re giving as a couple), the charity receives the remainder of the gift.</p>
  </article>

  <article class="panel col">
    <div class="feature" style="margin-top:-3px">
      <svg class="badge"><use href="#badge-ring"/><use href="#ic-coin" x="9" y="9" width="34" height="34"/></svg>
      <div>
        <h3 class="feature__title" style="font-size:10.3px">Cryptocurrency<br>Strategic &amp; Smart</h3>
        <p class="feature__pitch">Consider donating digital coins and other cryptocurrencies to your favorite charity.</p>
      </div>
    </div>
    <p class="body body--lg">Digital coins and other cryptocurrencies can be donated to charity just like other appreciated assets such as stocks and other business interests. Before you sell your coins &amp; donate the after-tax proceeds, consider donating your coins directly to a favorite charity.</p>
    <h4 class="how">How Does It Work?</h4>
    <p class="body">Many donors find it useful to open a Donor-Advised Fund (DAF). This strategy includes two significant benefits, both for you and your favorite charity.</p>
    <ul class="bullets">
      <li><svg><use href="#ic-tick"/></svg>Your tax deduction will be equal to the fair market value of the donated coins (as determined by a qualified appraisal).</li>
      <li><svg><use href="#ic-tick"/></svg>Your cryptocurrency donation is tax-smart because it may eliminate capital gains taxes on the value / appreciation AND your favorite charity will receive 100% of the value of the contribution.</li>
    </ul>
    <p class="body" style="margin-top:4px">Often charities are not able to accept direct donations of crypto so using a DAF is a great way to donate these assets.</p>
    <div class="photo" style="top:362px;height:154px;background:linear-gradient(115deg,#3f4a3a 0%,#a9987e 35%,#d8c6b0 55%,#8c6a4c 80%,#4a3a2c 100%)" role="img" aria-label="Photo of an elderly woman and a younger woman sharing a warm smile outdoors"></div>
    <svg class="curve" style="top:356px" viewBox="0 0 229 34" preserveAspectRatio="none" aria-hidden="true">
      <path d="M0 0H229V24Q114 -6 0 24Z" fill="#fff"/>
      <path d="M0 24Q114 -6 229 24Q114 0 0 24Z" fill="#4cb748"/>
    </svg>
  </article>
</section>
</body>
</html>
```